Brochure for new townhouse development

We need a brochure created for our new townhouse development that we can provide to potential purchasers for off-the-plan sales.

2 similar examples are attached.

Brochure content is to include the text as per the attached word document (brochure text) and as follows:
Cover
The Development
At a Glance
The Location - also to include the 2d map and aerial photo (have included screenshot of map and aerial photo as a placeholder, to be replaced in the final version)
Plans - include 3d floor plans, I have included a sample 3d floor plan as a placeholder, this is to be replaced in the final version.
Finishes - as per word document attached, and colour samples attached
Specifications - as per word document attached
Subdivision plan - I have attached a plan which can be used as a placeholder, the final version will be ready next week and is to be replaced in the final version
Landscape plan - as per attached
Rental assessment - as per attached
Stake your Claim

Renders of the building are attached and can be used throughout the brochure.

There is no company name or logo to include.

We have other upcoming developments and would look to reuse the winning brochure so there is future and ongoing work.

```html
<!DOCTYPE html>
<html lang="en">
<head>
<meta charset="utf-8">
<title>Townhouse Development Brochure – Cover</title>
<link rel="stylesheet" href="https://fonts.googleapis.com/css2?family=Montserrat:wght@300;700&display=swap">
<style>
  :root {
    --paper: #ffffff;
    --accent-blue: #1ba3e6;
    --frame-blue: #1a9fe3;
    --navy: #0d3b74;
    --sky-top: #bfe2f7;
    --sky-low: #e4e4ef;
    --timber: #b89a74;
    --render-white: #e9e7ea;
    --hedge: #4f6b3a;
    --path: #c9cbd0;
  }
  * { margin: 0; padding: 0; box-sizing: border-box; }
  html, body {
    width: 1200px;
    height: 849px;
    overflow: hidden;
    background: var(--paper);
  }
  .cover {
    position: relative;
    width: 1200px;
    height: 849px;
    background: var(--paper);
    font-family: "Montserrat", sans-serif;
  }
  .cover__render {
    position: absolute;
    left: 0;
    top: 0;
    width: 723px;
    height: 849px;
    background: linear-gradient(
      180deg,
      var(--sky-top) 0%,
      var(--sky-low) 28%,
      var(--timber) 45%,
      var(--timber) 62%,
      var(--render-white) 72%,
      var(--hedge) 86%,
      var(--path) 92%,
      var(--path) 100%
    );
  }
  .address-tag {
    position: absolute;
    left: 677px;
    top: 320px;
    width: 445px;
    height: 48px;
  }
  .address-tag svg {
    position: absolute;
    inset: 0;
  }
  .address-tag__text {
    position: absolute;
    left: 83px;
    top: 0;
    height: 48px;
    line-height: 48px;
    font-weight: 700;
    font-size: 22px;
    color: var(--navy);
    letter-spacing: 0.2px;
  }
  .cover__headline {
    position: absolute;
    left: 757px;
    top: 386px;
    font-weight: 300;
    font-size: 51px;
    line-height: 51px;
    color: var(--accent-blue);
    text-transform: uppercase;
    letter-spacing: 0.5px;
  }
</style>
</head>
<body>
  <main class="cover">
    <div class="cover__render" role="img" aria-label="Architectural render of a two-storey timber-clad gabled townhouse with a white rendered front wall, hedge and footpath under a pale blue sky"></div>

    <div class="address-tag">
      <svg width="445" height="48" viewBox="0 0 445 48" aria-hidden="true">
        <rect x="1" y="1" width="443" height="46" fill="var(--paper)" stroke="var(--frame-blue)" stroke-width="2"/>
        <polygon points="46,0 46,48 0,48" fill="var(--frame-blue)"/>
      </svg>
      <span class="address-tag__text">48 Larkfield Road</span>
    </div>

    <h1 class="cover__headline">Perfectly<br>Positioned<br>Urban Living</h1>
  </main>
</body>
</html>
```